Local Flower Farm Needs Business Card Design

I need business cards designed for a flower farm based in Eudora, Kansas.
Business Info:
We are a local cut flower farm located in Eudora, Kansas, founded by Corinne Haldwick. What started as a passion for agriculture and search for more joy in daily life has blossomed into a small business dedicated to providing the community with beautiful, fresh, and sustainable flowers. We specialize in local, seasonal blooms, ensuring that every petal reflects the care and dedication we pour into our craft. Our mission is to deliver the highest quality flowers directly to our customers through local farmers markets and to florists who share our commitment to sustainability. Join us in celebrating the beauty of nature, one bloom at a time!
Contact Details:
Corinne Haldwick
Owner
Phone 913-555-0147
Facebook: Rosalind Thorpe Gardens
Instagram: @RosalindThorpeGardens
Website: RosalindThorpeGardens.example
Target Market(s)
Wholesale to Florists and Direct to Consumer via Farmers Market
Industry/Entity Type
Florist, Farm
Contact Information for Business Card
Name, Contact Info, Logo
Look and feel
Each slider illustrates characteristics of the customer's brand and the style your logo design should communicate.

```html
<!DOCTYPE html>
<html lang="en">
<head>
<meta charset="utf-8">
<title>Rosalind Thorpe Gardens – Business Card</title>
<link rel="stylesheet" href="https://fonts.googleapis.com/css2?family=Montserrat:wght@400;500;800&display=swap">
<style>
  :root {
    --backdrop: #1c1c1c;
    --teal-deep: #0d272b;
    --teal-light: #2f4d51;
    --ink: #0f2b2f;
    --paper: #ffffff;
    --rule: #8a9a9b;
  }
  html, body {
    margin: 0;
    width: 1200px;
    height: 988px;
    overflow: hidden;
    background: var(--backdrop);
    font-family: "Montserrat", sans-serif;
  }
  .canvas {
    position: relative;
    width: 1200px;
    height: 988px;
  }
  .card {
    position: absolute;
    left: 240px;
    width: 720px;
    height: 411px;
    border-radius: 22px;
    overflow: hidden;
  }
  .card--back {
    top: 50px;
    background: var(--teal-deep);
  }
  .card--front {
    top: 527px;
    background: var(--paper);
  }
  .texture {
    position: absolute;
    inset: 0;
    background: linear-gradient(125deg, var(--teal-light) 0%, #22403f 35%, var(--teal-deep) 62%);
  }
  .brand-mark {
    position: absolute;
    left: 50%;
    transform: translateX(-50%);
    display: flex;
    align-items: center;
    justify-content: center;
    border-radius: 50%;
    text-align: center;
    font-weight: 500;
    letter-spacing: 0.12em;
    text-transform: uppercase;
    box-sizing: border-box;
  }
  .card--back .brand-mark {
    top: 75px;
    width: 260px;
    height: 260px;
    border: 1.5px solid var(--paper);
    color: var(--paper);
    font-size: 22px;
    line-height: 1.5;
  }
  .card--front .brand-mark {
    top: 40px;
    width: 180px;
    height: 180px;
    border: 1.2px solid var(--ink);
    color: var(--ink);
    font-size: 15px;
    line-height: 1.5;
  }
  .holder {
    position: absolute;
    right: 400px;
    top: 262px;
    text-align: right;
    color: var(--ink);
  }
  .holder__name {
    font-weight: 800;
    font-size: 27px;
    letter-spacing: 0.02em;
    text-transform: uppercase;
  }
  .holder__title {
    font-size: 13px;
    letter-spacing: 0.06em;
    text-transform: uppercase;
    margin-top: 2px;
  }
  .divider {
    position: absolute;
    left: 346px;
    top: 248px;
    width: 1px;
    height: 74px;
    background: var(--rule);
  }
  .contact {
    position: absolute;
    left: 368px;
    top: 244px;
    margin: 0;
    padding: 0;
    list-style: none;
    color: var(--ink);
    font-size: 14px;
  }
  .contact li {
    display: flex;
    align-items: center;
    gap: 8px;
    height: 26px;
  }
  .contact svg {
    width: 13px;
    height: 13px;
    fill: var(--ink);
    flex: none;
  }
  .social-band {
    position: absolute;
    left: 0;
    right: 0;
    bottom: 30px;
    height: 34px;
    background: var(--ink);
    color: var(--paper);
    font-size: 14px;
    display: flex;
    align-items: center;
    justify-content: center;
    gap: 10px;
  }
  .social-band .dot {
    width: 11px;
    height: 11px;
    border-radius: 50%;
    background: var(--paper);
  }
  .social-band .sep {
    width: 1px;
    height: 16px;
    background: var(--paper);
  }
</style>
</head>
<body>
<main class="canvas">
  <section class="card card--back">
    <div class="texture" role="img" aria-label="Soft diagonal teal texture across the card"></div>
    <div class="brand-mark">Rosalind<br>Thorpe<br>Gardens</div>
  </section>

  <section class="card card--front">
    <div class="brand-mark">Rosalind<br>Thorpe<br>Gardens</div>

    <div class="holder">
      <div class="holder__name">Corinne Haldwick</div>
      <div class="holder__title">Owner</div>
    </div>

    <div class="divider"></div>

    <ul class="contact">
      <li>
        <svg viewBox="0 0 24 24"><path d="M6.6 10.8a15.1 15.1 0 0 0 6.6 6.6l2.2-2.2a1 1 0 0 1 1-.25 11.4 11.4 0 0 0 3.6.57 1 1 0 0 1 1 1V20a1 1 0 0 1-1 1A17 17 0 0 1 3 4a1 1 0 0 1 1-1h3.5a1 1 0 0 1 1 1c0 1.25.2 2.45.57 3.57a1 1 0 0 1-.25 1z"/></svg>
        913-555-0147
      </li>
      <li>
        <svg viewBox="0 0 24 24"><path d="M2 5h20v14H2z M2 5l10 8 10-8" fill="none" stroke="#0f2b2f" stroke-width="2"/></svg>
        info@RosalindThorpeGardens.example
      </li>
      <li>
        <svg viewBox="0 0 24 24"><circle cx="12" cy="12" r="9" fill="none" stroke="#0f2b2f" stroke-width="2"/><path d="M3 12h18M12 3c3 3 3 15 0 18M12 3c-3 3-3 15 0 18" fill="none" stroke="#0f2b2f" stroke-width="1.6"/></svg>
        www.RosalindThorpeGardens.example
      </li>
    </ul>

    <div class="social-band">
      <span>Rosalind Thorpe Gardens</span>
      <span class="dot"></span>
      <span class="sep"></span>
      <span class="dot"></span>
      <span>@RosalindThorpeGardens</span>
    </div>
  </section>
</main>
</body>
</html>
```